Dovecote Realty

Business cards for 4 people

They need to say for all
87 Tarrow Quay, Boston MA 02114

Each person will have their own personal information
We would like gold embossing for the name of the company
Marla is the blonde sitting in the chair smiling her information should be on the back of the card with her name and information
Should say for slogan classic pattern, elevated experience
grace@dovecoteprops.com
(413) 555-0182

Odette is the brunette with wavy hair in the tan suit odette@dovecoteprops.com
(617) 555-0137

faith@dovecoteprops.com
(413) 555-0164
standing next to the chair

hope@dovecoteprops.com
(413) 555-0199
close up headshot

```html
<!DOCTYPE html>
<html lang="en">
<head>
<meta charset="utf-8">
<title>Dovecote Realty – Business Cards</title>
<link href="https://fonts.googleapis.com/css2?family=Open+Sans:wght@400;600;700&display=swap" rel="stylesheet">
<style>
  :root {
    --backdrop: #2a2b2f;
    --card: #1f2024;
    --gold: #e8b85c;
    --emboss: #111215;
    --text-light: #f1f1f1;
    --photo-light: #8a6440;
    --photo-dark: #2b2a2c;
  }
  * { margin: 0; padding: 0; box-sizing: border-box; }
  html, body {
    width: 1200px; height: 780px; overflow: hidden;
    background: var(--backdrop);
    font-family: "Open Sans", sans-serif;
  }
  .stage {
    width: 1200px; height: 780px;
    display: flex; align-items: center; justify-content: center; gap: 40px;
  }
  .card {
    position: relative;
    width: 540px; height: 309px;
    background: var(--card);
    border: 2px solid var(--gold);
    overflow: hidden;
  }
  /* Front */
  .card-front { display: flex; align-items: center; justify-content: center; }
  .front-mark { display: flex; align-items: center; gap: 18px; }
  .front-mark .ring {
    width: 70px; height: 70px; border-radius: 50%;
    border: 3px solid var(--emboss);
  }
  .front-mark .brand {
    color: var(--emboss); font-weight: 700;
    font-size: 40px; letter-spacing: 1px; text-transform: uppercase;
  }
  /* Back */
  .photo-area {
    position: absolute; right: 0; top: 40px;
    width: 205px; height: 269px;
    background: radial-gradient(ellipse at 45% 40%, var(--photo-light) 0%, #5c4430 45%, var(--photo-dark) 85%);
  }
  .back-info { position: absolute; left: 0; top: 34px; width: 310px; }
  .back-mark { display: flex; align-items: center; gap: 10px; margin-left: 34px; }
  .back-mark .ring {
    width: 34px; height: 34px; border-radius: 50%;
    border: 2px solid var(--gold); flex: none;
  }
  .back-mark .brand {
    color: var(--gold); font-weight: 600;
    font-size: 19px; letter-spacing: 1px; text-transform: uppercase;
    white-space: nowrap;
  }
  .identity { position: relative; margin-top: 26px; padding-left: 34px; }
  .identity::before {
    content: ""; position: absolute; left: 0; top: 4px;
    width: 22px; height: 42px; background: var(--gold);
  }
  .person-name { color: var(--gold); font-weight: 700; font-size: 25px; line-height: 1.1; white-space: nowrap; }
  .person-title { color: var(--text-light); font-weight: 600; font-size: 11.5px; margin-top: 3px; white-space: nowrap; }
  .address { color: var(--text-light); font-size: 13px; line-height: 1.35; margin: 14px 0 0 34px; }
  .contacts { list-style: none; margin: 12px 0 0 34px; }
  .contacts li {
    display: flex; align-items: center; gap: 8px;
    color: var(--text-light); font-size: 13px; line-height: 1.55; white-space: nowrap;
  }
  .contacts svg { width: 12px; height: 12px; flex: none; }
</style>
</head>
<body>
<main class="stage">
  <section class="card card-front" aria-label="Card front">
    <div class="front-mark">
      <span class="ring"></span>
      <span class="brand">Dovecote Realty</span>
    </div>
  </section>

  <section class="card card-back" aria-label="Card back">
    <div class="photo-area" role="img" aria-label="Portrait photo of Odette, brunette with wavy hair in a tan suit"></div>
    <div class="back-info">
      <div class="back-mark">
        <span class="ring"></span>
        <span class="brand">Dovecote Realty</span>
      </div>
      <div class="identity">
        <h1 class="person-name">Odette Marchand</h1>
        <p class="person-title">Real Estate Advisor and Sales Manager</p>
      </div>
      <p class="address">87 Tarrow Quay,<br>Boston MA 02114</p>
      <ul class="contacts">
        <li>
          <svg viewBox="0 0 24 24" aria-hidden="true"><path fill="#e8b85c" d="M6.6 10.8a15.1 15.1 0 0 0 6.6 6.6l2.2-2.2a1 1 0 0 1 1-.25 11.4 11.4 0 0 0 3.6.6 1 1 0 0 1 1 1V20a1 1 0 0 1-1 1A17 17 0 0 1 3 4a1 1 0 0 1 1-1h3.5a1 1 0 0 1 1 1c0 1.25.2 2.45.6 3.6a1 1 0 0 1-.25 1z"/></svg>
          (617) 555-0137
        </li>
        <li>
          <svg viewBox="0 0 24 24" aria-hidden="true"><circle cx="12" cy="12" r="9" fill="none" stroke="#e8b85c" stroke-width="2.4"/><path d="M3 12h18M12 3c3 3 3 15 0 18M12 3c-3 3-3 15 0 18" fill="none" stroke="#e8b85c" stroke-width="2"/></svg>
          www.dovecoteprops.com
        </li>
        <li>
          <svg viewBox="0 0 24 24" aria-hidden="true"><rect x="2" y="5" width="20" height="14" rx="1.5" fill="#e8b85c"/><path d="M3 6l9 7 9-7" fill="none" stroke="#1f2024" stroke-width="2"/></svg>
          odette@dovecoteprops.com
        </li>
      </ul>
    </div>
  </section>
</main>
</body>
</html>
```